Interior Design/ decoration business card design

This card is for my Interior Design and Decoration business and later I will also be selling homewares. I would like the card to be very simple in design and like either white, duck egg blue , aquas or metallics on a flat mat card excellent quality card. It needs to be well designed as that is my field. I dont like fuss, the simpler the better. I would like a styalised brim under the name brim if possible. SIMPLE, STYLISH, CLASSIC, TASTEFUL

Target Market(s)

40 + year olds who are building or rennovating.

Industry/Entity Type

Business

Contact Information for Business Card

Brim
styling, design, homeware

Marnie Callow
p 0427163958
e marnie@brimhouse.com.au
w brimhouse.com.au

Requirements
Must have
• very simple, stylish, classic, sophisticated. Simple and easy to read text that is a print similar to attached image. I like simple round A's though not as in attached image.

Double sided. It wont save as double sided for some reason!!
Should not have
• not too much colour, No animated / cartoon pictures.

```html
<!DOCTYPE html>
<html lang="en">
<head>
<meta charset="utf-8">
<title>Brim — business card, back and front</title>
<link href="https://fonts.googleapis.com/css2?family=Questrial&family=Montserrat:wght@700&display=swap" rel="stylesheet">
<style>
  :root {
    --backdrop: #ecebe8;
    --card: #ffffff;
    --duck-egg: #a9d2d1;
    --duck-egg-deep: #8fc2c1;
    --ink: #4a3b34;
    --ink-soft: #3d3d3d;
  }
  * { box-sizing: border-box; margin: 0; padding: 0; }
  html, body {
    width: 1200px; height: 609px; overflow: hidden;
    background: var(--backdrop);
    font-family: "Questrial", Arial, sans-serif;
    color: var(--ink-soft);
  }
  .stage {
    position: relative; width: 1200px; height: 609px;
    display: flex; align-items: center; justify-content: center; gap: 60px;
  }
  .card {
    position: relative; width: 520px; height: 318px;
    background: var(--card);
    box-shadow: 0 6px 18px rgba(0,0,0,0.12);
  }
  .card__frame {
    position: absolute; inset: 10px;
    border: 2px solid var(--duck-egg);
  }

  /* back: contact side */
  .card--back .holder {
    position: absolute; top: 30px; right: 40px; text-align: right;
  }
  .holder__name {
    font-family: "Montserrat", Arial, sans-serif; font-weight: 700;
    font-size: 14px; color: var(--duck-egg);
  }
  .holder__role { font-size: 13px; color: var(--ink-soft); margin-top: 1px; }

  .brand { text-align: center; }
  .brand__name {
    font-size: 48px; line-height: 1; color: var(--ink);
    letter-spacing: 1px;
  }
  .brand__tagline { color: var(--ink-soft); white-space: nowrap; }
  .brand__tagline .bar {
    display: inline-block; width: 2px; background: var(--ink);
    vertical-align: -3px; margin: 0 4px;
  }

  .card--back .brand {
    position: absolute; left: 40px; top: 122px; width: 210px;
  }
  .card--back .brand__tagline { font-size: 13.5px; margin-top: 18px; }
  .card--back .brand__tagline .bar { height: 16px; }

  .divider {
    position: absolute; left: 282px; top: 118px;
    width: 3px; height: 86px; background: var(--duck-egg);
  }
  .contacts {
    position: absolute; left: 318px; top: 123px;
    list-style: none; font-size: 12.5px; color: var(--ink-soft);
  }
  .contacts li { display: flex; align-items: center; gap: 9px; height: 24px; }
  .contacts svg { width: 14px; height: 14px; flex: none; }

  /* front: brand side */
  .card--front .brand {
    position: absolute; left: 0; right: 0; top: 104px;
  }
  .card--front .brand__name { font-size: 72px; }
  .card--front .brand__tagline { font-size: 19px; margin-top: 24px; }
  .card--front .brand__tagline .bar { height: 22px; vertical-align: -4px; }
</style>
</head>
<body>
<main class="stage">

  <section class="card card--back" aria-label="Card back, contact details">
    <div class="card__frame"></div>
    <div class="holder">
      <p class="holder__name">Marnie Callow</p>
      <p class="holder__role">Homeware Expert</p>
    </div>
    <div class="brand">
      <p class="brand__name">brim</p>
      <p class="brand__tagline">decoration<span class="bar"></span>styling<span class="bar"></span>homeware</p>
    </div>
    <div class="divider"></div>
    <ul class="contacts">
      <li>
        <svg viewBox="0 0 14 14" aria-hidden="true"><rect width="14" height="14" rx="2" fill="var(--duck-egg)"/><rect x="4.5" y="2.5" width="5" height="9" rx="1" fill="none" stroke="#fff" stroke-width="1.2"/></svg>
        0427 163 958
      </li>
      <li>
        <svg viewBox="0 0 14 14" aria-hidden="true"><rect width="14" height="14" rx="2" fill="var(--duck-egg)"/><rect x="2.5" y="4" width="9" height="6" fill="none" stroke="#fff" stroke-width="1.1"/><path d="M2.5 4 L7 7.5 L11.5 4" fill="none" stroke="#fff" stroke-width="1.1"/></svg>
        marnie@brimhouse.com.au
      </li>
      <li>
        <svg viewBox="0 0 14 14" aria-hidden="true"><rect width="14" height="14" rx="2" fill="var(--duck-egg)"/><circle cx="7" cy="7" r="4.3" fill="none" stroke="#fff" stroke-width="1.1"/><ellipse cx="7" cy="7" rx="1.8" ry="4.3" fill="none" stroke="#fff" stroke-width="1"/><line x1="2.7" y1="7" x2="11.3" y2="7" stroke="#fff" stroke-width="1"/></svg>
        brimhouse.com.au
      </li>
    </ul>
  </section>

  <section class="card card--front" aria-label="Card front, brand">
    <div class="card__frame"></div>
    <div class="brand">
      <p class="brand__name">brim</p>
      <p class="brand__tagline">decoration<span class="bar"></span>styling<span class="bar"></span>homeware</p>
    </div>
  </section>

</main>
</body>
</html>
```